Postcard design to acquire new clients for my Property Management Company

I'm looking for a postcard design that I can send to prospective clients detailing information about my company and services.
Postcard should be eye catching and contain information from www.bramblecrestpm.com. I've provided a few screen shots for the most important information and my logo.
Target Market(s)
Real Estate
Industry/Entity Type
Real Estate
Font styles to use
Sans Serif
Requirements
Must have
- Must be eye catching!! this will be a direct mail piece - I'd like for the card to be read and not tossed in the trash immediately.
Design que from the logo.
A place to write / print the receipts name and address.
our physical address - 2387 Hollow Pine Road, Lubbock, TX 79852.
Should not have
- the contact information on the business card is not accurate - please use info from website.

```html
<!DOCTYPE html>
<html lang="en">
<head>
<meta charset="utf-8">
<title>Bramblecrest Property Management Postcard</title>
<link rel="stylesheet" href="https://fonts.googleapis.com/css2?family=Montserrat:wght@400;500;600;700;800;900&display=swap">
<style>
  :root {
    --page-bg: #333334;
    --navy: #134f86;
    --slate: #3f4a5c;
    --ink: #0d0d0d;
    --grey-text: #4d4d4d;
    --white: #ffffff;
    --mail-grey: #a4a4a4;
    --rule: #1b1b1b;
  }
  * { margin: 0; padding: 0; box-sizing: border-box; }
  html, body { width: 1200px; height: 650px; overflow: hidden; }
  body {
    background: var(--page-bg);
    font-family: "Montserrat", sans-serif;
    position: relative;
  }
  .postcard {
    position: absolute;
    top: 138px;
    width: 560px;
    height: 374px;
    overflow: hidden;
    background: var(--white);
  }
  .postcard--front { left: 30px; }
  .postcard--back { left: 610px; }
  .postcard__shapes { position: absolute; inset: 0; width: 560px; height: 374px; }

  /* Front */
  .brand { position: absolute; right: 14px; top: 9px; text-align: right; color: var(--navy); }
  .brand__name { font-size: 24px; font-weight: 700; letter-spacing: 6px; line-height: 26px; margin-right: -6px; }
  .brand__tag { font-size: 13px; font-weight: 500; letter-spacing: 3.6px; line-height: 16px; margin-right: -3.6px; margin-top: 3px; }

  .headline { position: absolute; right: 13px; top: 86px; text-align: right; }
  .headline__main { font-size: 47px; font-weight: 900; color: var(--ink); line-height: 48px; letter-spacing: -0.5px; }
  .headline__sub { font-size: 32px; font-weight: 700; color: var(--navy); line-height: 38px; }
  .headline__place { font-size: 26px; font-weight: 600; color: var(--ink); line-height: 32px; letter-spacing: -0.3px; }
  .headline__rule { position: absolute; left: 507px; top: 201px; width: 53px; height: 2px; background: var(--navy); }

  .pitch { position: absolute; right: 14px; top: 226px; text-align: right; font-size: 13.5px; font-weight: 500; line-height: 16px; color: var(--grey-text); }

  .contact__label { position: absolute; left: 231px; top: 298px; font-size: 15px; font-weight: 700; color: var(--ink); line-height: 17px; }
  .contact__line { position: absolute; font-size: 15.5px; color: var(--white); line-height: 17px; white-space: nowrap; }
  .contact__line--call { left: 246px; top: 315px; }
  .contact__line--email { left: 259px; top: 332px; }
  .contact__line--web { left: 269px; top: 349px; }

  /* Back */
  .services-title { position: absolute; left: 0; top: 10px; width: 280px; text-align: center; font-size: 17px; font-weight: 800; color: var(--white); line-height: 22px; }
  .service { position: absolute; width: 128px; }
  .service__icon { position: absolute; left: -30px; top: 0; width: 24px; height: 22px; }
  .service__name { font-size: 12.5px; font-weight: 600; color: var(--navy); line-height: 16px; white-space: nowrap; }
  .service__text { font-size: 7.6px; font-weight: 500; color: var(--ink); line-height: 7.9px; margin-top: 2px; }
  .service__text--loose { line-height: 9.6px; margin-top: 3px; }

  .back-slogan { position: absolute; left: 0; top: 303px; width: 345px; text-align: center; font-size: 18.5px; font-weight: 600; color: var(--white); line-height: 22px; }
  .back-address { position: absolute; left: 0; top: 351px; width: 345px; text-align: center; font-size: 10.5px; font-weight: 500; color: var(--white); line-height: 13px; }
</style>
</head>
<body>

<section class="postcard postcard--front" aria-label="Postcard front">
  <svg class="postcard__shapes" viewBox="0 0 1121 747">
    <rect width="1121" height="747" fill="var(--white)"/>
    <polygon points="0,0 545,0 448,150 0,150" fill="var(--slate)"/>
    <polygon points="0,627 461,627 540,747 0,747" fill="var(--slate)"/>
    <polygon points="461,627 1121,627 1121,747 540,747" fill="var(--navy)"/>
    <defs>
      <linearGradient id="towerTones" x1="0" y1="0" x2="1" y2="1">
        <stop offset="0" stop-color="#d2e2ec"/>
        <stop offset="0.35" stop-color="#4b8c9c"/>
        <stop offset="1" stop-color="#16525f"/>
      </linearGradient>
    </defs>
    <g role="img" aria-label="Photo of a glass office tower against a pale sky">
      <polygon points="0,45 390,45 580,372 390,708 0,708" fill="url(#towerTones)"/>
    </g>
    <polyline points="390,45 580,372 390,708" fill="none" stroke="var(--navy)" stroke-width="3"/>
  </svg>

  <div class="brand">
    <div class="brand__name">BRAMBLECREST</div>
    <div class="brand__tag">PROPERTY MANAGEMENT</div>
  </div>

  <div class="headline">
    <div class="headline__main">PROPERTY</div>
    <div class="headline__sub">MANAGEMENT</div>
    <div class="headline__place">ACROSS LUBBOCK</div>
  </div>
  <div class="headline__rule"></div>

  <p class="pitch">Maximize your financial returns with<br>support from our rental specialists</p>

  <div class="contact__label">Contact us;</div>
  <div class="contact__line contact__line--call">Call: (806) 555-0147</div>
  <div class="contact__line contact__line--email">Email: info@bramblecrestpm.com</div>
  <div class="contact__line contact__line--web">Web: bramblecrestpm.com</div>
</section>

<section class="postcard postcard--back" aria-label="Postcard back">
  <svg class="postcard__shapes" viewBox="0 0 1121 747">
    <rect width="1121" height="747" fill="var(--white)"/>
    <rect x="668" y="0" width="453" height="747" fill="var(--mail-grey)"/>
    <polygon points="0,18 540,18 572,62 0,62" fill="var(--navy)"/>
    <rect x="936" y="20" width="157" height="170" fill="none" stroke="var(--navy)" stroke-width="3"/>
    <line x1="708" y1="275" x2="1093" y2="275" stroke="var(--rule)" stroke-width="2"/>
    <line x1="708" y1="375" x2="1093" y2="375" stroke="var(--rule)" stroke-width="2"/>
    <line x1="708" y1="495" x2="1093" y2="495" stroke="var(--rule)" stroke-width="2"/>
    <polygon points="0,578 918,578 1002,747 0,747" fill="var(--navy)"/>
  </svg>

  <div class="services-title">OUR SERVICES</div>

  <div class="service" style="left:38px; top:48px;">
    <svg class="service__icon" viewBox="0 0 24 22"><path d="M12 1 L1 11 L4 11 L4 21 L10 21 L10 15 L14 15 L14 21 L20 21 L20 11 L23 11 Z" fill="var(--navy)"/></svg>
    <div class="service__name">Property Marketing</div>
    <p class="service__text service__text--loose">Let us take over your marketing for you and we'll find a quali-fied renter quickly.</p>
  </div>

  <div class="service" style="left:39px; top:102px;">
    <svg class="service__icon" viewBox="0 0 24 22"><circle cx="8" cy="6" r="4.5" fill="var(--navy)"/><circle cx="18" cy="6" r="4" fill="var(--navy)"/><path d="M0 19 Q0 12 8 12 Q16 12 16 19 Z" fill="var(--navy)"/><path d="M14 12 Q24 10 24 18 L17 18 Q17 14 14 12 Z" fill="var(--navy)"/></svg>
    <div class="service__name">Tenant Screening</div>
    <p class="service__text">We don't just find someone to rent your home—we find the best renters. We screen all ap-plications using fair housing guidelines to protect you.</p>
  </div>

  <div class="service" style="left:38px; top:162px;">
    <svg class="service__icon" viewBox="0 0 24 22"><text x="5" y="19" font-family="Montserrat, sans-serif" font-weight="700" font-size="22" fill="var(--navy)">$</text></svg>
    <div class="service__name">Rent Collection</div>
    <p class="service__text">Stop guessing when you'll re-ceive your rental earnings every month and say hello to consis-tent payments. We keep your tenants current.</p>
  </div>

  <div class="service" style="left:38px; top:225px;">
    <svg class="service__icon" viewBox="0 0 24 22"><rect x="9" y="2" width="13" height="6" rx="1" fill="var(--navy)" transform="rotate(35 15 5)"/><rect x="2" y="8" width="3.5" height="15" fill="var(--navy)" transform="rotate(45 4 15)"/></svg>
    <div class="service__name">Maintenance</div>
    <p class="service__text">Still scrambling to respond to repair requests every time you receive a tenant call? Let us co-ordinate repair work on your behalf!</p>
  </div>

  <div class="service" style="left:193px; top:46px;">
    <svg class="service__icon" viewBox="0 0 24 22"><circle cx="10" cy="9" r="7" fill="none" stroke="var(--navy)" stroke-width="3"/><line x1="15" y1="14" x2="22" y2="21" stroke="var(--navy)" stroke-width="3.5" stroke-linecap="round"/></svg>
    <div class="service__name">Property Inspections</div>
    <p class="service__text">We visit every home in our portfolio regularly.</p>
  </div>

  <div class="service" style="left:193px; top:91px;">
    <svg class="service__icon" viewBox="0 0 24 22"><path d="M1 2 V20 H23" fill="none" stroke="var(--navy)" stroke-width="2"/><rect x="5" y="10" width="2" height="8" fill="var(--navy)"/><rect x="10" y="6" width="2" height="12" fill="var(--navy)"/><rect x="15" y="11" width="2" height="7" fill="var(--navy)"/><rect x="20" y="4" width="2" height="14" fill="var(--navy)"/></svg>
    <div class="service__name">Financial Reporting</div>
    <p class="service__text">Keep a handle on your real estate performance. We generate monthly statements so you can review income &amp; expenses at a moment's notice.</p>
  </div>

  <div class="service" style="left:193px; top:157px;">
    <svg class="service__icon" viewBox="0 0 24 22"><path d="M12 1 L22 4 V10 Q22 18 12 22 Q2 18 2 10 V4 Z" fill="var(--navy)"/><path d="M12 4 L19 6 V10 Q19 16 12 19 Z" fill="var(--white)"/></svg>
    <div class="service__name">Evictions</div>
    <p class="service__text">When things go wrong inside your rental home, rest easy with the experts on your side. We will handle evictions for you &amp; find new renters when its over.</p>
  </div>

  <div class="service" style="left:193px; top:222px;">
    <svg class="service__icon" viewBox="0 0 24 22"><line x1="12" y1="1" x2="12" y2="20" stroke="var(--navy)" stroke-width="2"/><line x1="3" y1="4" x2="21" y2="4" stroke="var(--navy)" stroke-width="2"/><path d="M1 13 L5 5 L9 13 Z M15 13 L19 5 L23 13 Z" fill="none" stroke="var(--navy)" stroke-width="1.6"/><rect x="7" y="19" width="10" height="2.5" fill="var(--navy)"/></svg>
    <div class="service__name">Legal Guidance</div>
    <p class="service__text">Don't accidentally violate one of the many ordinances and hous-ing laws governing your relation-ship with your tenants. Let us keep you compliant.</p>
  </div>

  <div class="back-slogan">CHOOSE THE RIGHT<br>PROPERTY MANAGEMENT SYSTEM</div>
  <div class="back-address">2387 Hollow Pine Road, Lubbock, TX 79852</div>
</section>

</body>
</html>
```